Current website re-design to a updated look and feel.

We currently have a website www.brightlanefreight.com that we want to give an updated look and feel to. We are a logistics company that competes with Pellwick, Dm Harrowgate, Quill but on a smaller scale. We want something fresh and updated. We have two locations one in downtown Chicago, IL and one in Palatine IL. We are a fun group that also gets the job done. We know we need pictures of both locations and possibly a video, but we need fresh design ideas. The 'who we are' page is really the only page that we currently want to keep. The 'what we do' page needs to be completely re-done from a look and feel for sure.

Target Market(s)

Anyone who uses Truck transportation to move their product. Mainly US manufacturers.

Industry/Entity Type

Logistics

Number of Pages Required

5+ page

Font styles to use
Sans Serif

Colors
5c91c4
0355a3
d0dfed

Requirements
Must have
• The new design must entice people to want to do business with us. The design must have locations for pictures and at least one video which we know we will have to provide. Design must be easy to navigate.

```html
<!DOCTYPE html>
<html lang="en">
<head>
<meta charset="utf-8">
<title>Brightlane Freight — Transportation, Distribution &amp; Warehousing</title>
<link rel="stylesheet" href="https://fonts.googleapis.com/css2?family=Cormorant+Garamond:wght@500;600&family=Open+Sans:wght@600;700;800&family=Roboto:wght@400;500;700&display=swap">
<style>
:root{
  --navy:#1d2c6b;
  --navy-deep:#162458;
  --royal:#0f3aa3;
  --brand:#0355a3;
  --sky:#5c91c4;
  --mist:#d0dfed;
  --teal:#54b3d6;
  --ink:#222;
  --body:#666;
  --white:#fff;
}
*{margin:0;padding:0;box-sizing:border-box}
html,body{width:1200px;height:2466px;overflow:hidden}
body{position:relative;background:var(--white);font-family:"Roboto",Arial,sans-serif;color:var(--body)}
.abs{position:absolute}

/* Hero */
.hero{left:0;top:0;width:1200px;height:677px;
  background:linear-gradient(180deg,#3a3f6a 0%,#a8465a 16%,#c55a55 26%,#5a5a78 44%,#3b4a66 58%,#5a4a40 75%,#3b3a36 100%)}
.site-header{left:77px;top:0;width:1046px;height:135px;background:rgba(255,255,255,.9)}
.brand{left:12px;top:26px;display:flex;align-items:center;gap:12px}
.brand-name{font-family:"Roboto",sans-serif;font-weight:400;font-size:50px;color:var(--brand);letter-spacing:-1px}
.brand-tag{font-size:11px;line-height:13px;color:var(--brand);font-weight:400;width:120px}
.contact-top{left:564px;top:22px;display:flex;align-items:center;font-size:15px;color:#999}
.contact-top span{display:flex;align-items:center;gap:10px}
.contact-top .sep{width:1px;height:26px;background:#bbb;margin:0 18px 0 42px}
.rule{left:390px;top:66px;width:643px;height:1px;background:#ccc}
.main-nav{left:386px;top:91px;display:flex;gap:32px;font-size:14px;color:#888;text-transform:uppercase;list-style:none}
.main-nav .active{color:#333}
.hero-copy{left:0;top:280px;width:1200px;text-align:center;color:var(--white);font-family:"Open Sans",sans-serif;text-shadow:0 2px 6px rgba(0,0,0,.35)}
.hero-copy h1{font-weight:700;font-size:62px;line-height:64px}
.hero-copy .sub{font-weight:700;font-size:42px;line-height:44px;margin-top:-2px}
.hero-copy .services{font-weight:700;font-size:23px;margin-top:8px;word-spacing:3px}

/* Section titles */
.section-title{width:1200px;left:0;text-align:center;font-family:"Cormorant Garamond",serif;font-weight:600;font-size:32px;color:var(--ink);letter-spacing:1px}

/* Mission */
.mission{left:145px;top:780px;width:910px;text-align:center}
.mission h3{font-size:18px;font-weight:700;color:#555;text-decoration:underline;margin-bottom:10px}
.mission p{font-size:14px;line-height:21px;color:#666;margin-bottom:30px}

/* Who we are */
.who{left:0;top:1047px;width:1200px;height:364px;background:linear-gradient(90deg,#24377a,#1d2c6b 60%,#22336f)}
.video-frame{left:77px;top:33px;width:580px;height:285px;border:2px solid var(--white)}
.video-thumb{left:95px;top:53px;width:581px;height:283px;background:linear-gradient(180deg,#6b5326 0%,#c68d2c 30%,#9a7a3a 52%,#3f4a2a 74%,#545a52 100%)}
.play{left:254px;top:103px}
.who-copy{left:740px;top:50px;width:383px;text-align:right;color:var(--white)}
.who-copy h2{font-family:"Cormorant Garamond",serif;font-weight:500;font-size:36px;color:var(--teal);letter-spacing:1px}
.who-copy p{font-size:15px;line-height:21px;margin-top:16px}
.btn{display:inline-flex;align-items:center;justify-content:center;background:var(--white);color:var(--navy);border-radius:30px;font-size:18px;font-weight:500;box-shadow:0 2px 0 rgba(0,0,0,.25)}
.who .btn{left:934px;top:262px;width:189px;height:52px}

/* What we do */
.service{top:1519px;width:235px;height:235px;overflow:hidden}
.service .photo{position:absolute;inset:0}
.service .caption{position:absolute;left:0;bottom:0;width:100%;height:50px;background:rgba(22,36,88,.75);color:var(--white);font-family:"Cormorant Garamond",serif;font-weight:600;font-size:19px;display:flex;align-items:center;justify-content:center}
.service.featured .photo{background:linear-gradient(180deg,#1a2340,#28304a 60%,#3a3a3a)}
.featured h4{position:absolute;left:14px;top:26px;font-family:"Open Sans",sans-serif;font-weight:700;font-size:20px;color:var(--white)}
.featured p{position:absolute;left:30px;top:76px;width:180px;text-align:center;font-size:14px;line-height:18px;color:var(--white)}
.featured .btn{position:absolute;left:36px;top:164px;width:160px;height:44px;font-size:18px}

/* Testimonial */
.arrow{top:1896px}
.avatar-back{left:536px;top:1868px;width:80px;height:80px;border-radius:50%;background:#c9c9c9}
.avatar{left:573px;top:1861px;width:92px;height:92px;border-radius:50%;background:linear-gradient(160deg,#7a4a30,#c48a6a 55%,#2c8a6a);border:3px solid var(--white)}
.quote{left:170px;top:1974px;width:860px;text-align:center;font-size:14.5px;line-height:22px;color:#666}
.quote-name{left:0;top:2052px;width:1200px;text-align:center;font-family:"Cormorant Garamond",serif;font-size:20px;color:var(--navy)}

/* Footer */
.site-footer{left:0;top:2127px;width:1200px;height:339px;background:var(--royal)}
.footer-col{top:52px}
.footer-col h5{font-family:"Cormorant Garamond",serif;font-weight:500;font-size:20px;color:var(--teal);margin-bottom:16px}
.footer-col ul{list-style:none;font-size:14px;line-height:29px;color:#d7e0f5;text-transform:uppercase}
.footer-col p{font-size:14px;line-height:24px;color:#d7e0f5}
.social{display:flex;gap:8px;margin-top:14px}
.social span{width:34px;height:34px;border:1px solid rgba(255,255,255,.35)}
.social span:first-child{background:var(--white)}
.news-field{margin-top:28px;display:flex;width:240px;height:36px;border:1px solid var(--white)}
.news-field span{flex:1;font-size:13px;color:var(--white);padding:8px 10px}
.news-field i{width:36px;background:#3a8fd0;display:flex;align-items:center;justify-content:center}
.touch-row{display:flex;gap:12px;font-size:14px;line-height:24px;color:#d7e0f5;margin-bottom:12px}
.touch-row svg{flex:none;margin-top:4px}
.copyright{left:77px;top:286px;width:1046px;height:53px;background:var(--white);text-align:center;font-size:14px;line-height:53px;color:var(--navy)}
.copyright b{font-weight:400;color:var(--brand)}
</style>
</head>
<body>

<section class="hero abs" role="img" aria-label="Harbour container terminal with cranes and stacked shipping containers under a red sunset sky"></section>

<header class="site-header abs">
  <div class="brand abs">
    <span class="brand-name">Brightlane</span>
    <span class="brand-tag">Transportation, Distribution &amp; Warehousing Inc.</span>
  </div>
  <div class="contact-top abs">
    <span><svg width="18" height="18" viewBox="0 0 24 24" fill="none" stroke="#888" stroke-width="2"><path d="M5 3h4l2 5-3 2a12 12 0 0 0 6 6l2-3 5 2v4a2 2 0 0 1-2 2A18 18 0 0 1 3 5a2 2 0 0 1 2-2z"/></svg>555.014.2200</span>
    <i class="sep"></i>
    <span><svg width="20" height="20" viewBox="0 0 24 24" fill="none" stroke="#888" stroke-width="2"><path d="M22 2 11 13M22 2l-7 20-4-9-9-4z"/></svg>info@brightlanefreight.com</span>
  </div>
  <div class="rule abs"></div>
  <ul class="main-nav abs">
    <li class="active">Home</li><li>What we do</li><li>Who we are</li><li>How we do it</li><li>Tracking</li><li>Contact us</li>
  </ul>
</header>

<div class="hero-copy abs">
  <h1>RELEX,</h1>
  <div class="sub">WE GOT THIS.</div>
  <div class="services">• Transportation • Distribution • Warehousing</div>
</div>

<h2 class="section-title abs" style="top:725px">OUR MISSION AND VISION</h2>
<div class="mission abs">
  <h3>Brightlane Mission</h3>
  <p>Brightlane’s mission is to provide the most thorough and satisfying third-party logistics experience for its customers. Brightlane uses leading technologies and an industry experienced staff to deliver an unparalleled customer service experience. Brightlane leverages the most efficient mode of transportation, and tailors cost effective solutions for warehousing and distribution of your products in every situation.</p>
  <h3>Brightlane Vision</h3>
  <p>Brightlane vision is to be the premier third party logistics solution in North America. We will become premier by providing superior customer service, efficient and cost effective warehousing and distribution solutions. The decisions we make today for hiring, training, technology, strategic services and customer satisfaction are based on this vision.</p>
</div>

<section class="who abs">
  <div class="video-frame abs"></div>
  <div class="video-thumb abs" role="img" aria-label="Video still: trucks on a highway through green hills at golden sunset">
    <svg class="play abs" width="76" height="76" viewBox="0 0 76 76"><rect x="2" y="2" width="72" height="72" rx="10" fill="rgba(255,255,255,.55)"/><rect x="14" y="14" width="48" height="48" rx="4" fill="none" stroke="#b5834a" stroke-width="5"/><path d="M30 24l20 14-20 14z" fill="#b5834a"/></svg>
  </div>
  <div class="who-copy abs">
    <h2>WHO WE ARE</h2>
    <p>Brightlane Freight welcomes you to our growing family of clients! We have over 26 years of experience in helping people solve their logistics needs from coast-to-coast. We also provide friendly, exceptional service that makes it easy to do business with us. Give us a call today and experience the difference for yourself!</p>
  </div>
  <span class="btn abs">READ MORE</span>
</section>

<h2 class="section-title abs" style="top:1460px">WHAT WE DO</h2>
<article class="service featured abs" style="left:77px">
  <div class="photo" role="img" aria-label="Dark photo of a logistics yard behind the card text"></div>
  <h4>Freight Management</h4>
  <p>We strive for a perfect delivery and promise to be there for anything you may...</p>
  <span class="btn">READ MORE</span>
</article>
<article class="service abs" style="left:349px">
  <div class="photo" role="img" aria-label="Highway light trails at dusk" style="background:linear-gradient(180deg,#2a3550,#7a5a50 35%,#3a3040 60%,#a33a3a 80%,#2a2a3a)"></div>
  <div class="caption">Product Transportation</div>
</article>
<article class="service abs" style="left:620px">
  <div class="photo" role="img" aria-label="Cardboard boxes loaded in the back of a delivery truck" style="background:linear-gradient(180deg,#e8e8e8,#d8c8a8 50%,#b08a5a 80%,#8a6a48)"></div>
  <div class="caption">Warehouse &amp; Distribution</div>
</article>
<article class="service abs" style="left:888px">
  <div class="photo" role="img" aria-label="Blue and purple semi trucks parked side by side" style="background:linear-gradient(180deg,#dfe6f0,#4a6ab0 40%,#6a4a9a 65%,#5a5a60)"></div>
  <div class="caption">Carriers</div>
</article>

<h2 class="section-title abs" style="top:1802px">TESTIMONIAL</h2>
<svg class="arrow abs" style="left:488px" width="12" height="18" viewBox="0 0 12 18"><path d="M10 2 3 9l7 7" fill="none" stroke="#1d2c6b" stroke-width="2.5"/></svg>
<svg class="arrow abs" style="left:707px" width="12" height="18" viewBox="0 0 12 18"><path d="M2 2l7 7-7 7" fill="none" stroke="#1d2c6b" stroke-width="2.5"/></svg>
<div class="avatar-back abs" role="img" aria-label="Previous client portrait"></div>
<div class="avatar abs" role="img" aria-label="Client portrait"></div>
<p class="quote abs">"Lorem ipsum dolor sit amet, consectetur adipiscing elit. Maecenas id est lacus. Fusce vitae sodales nibh. Vivamus auctor erat vitae risus consequat maximus.Quisque laoreet vitae odio at malesuada. Vivamus fringilla, erat vitae maximus maximus, erat mi lacinia dui, in ultricies nibh ipsum nec ligula. "</p>
<div class="quote-name abs">- Name</div>

<footer class="site-footer abs">
  <div class="footer-col abs" style="left:79px">
    <h5>Usefull Links</h5>
    <ul><li>Home</li><li>About us</li><li>Services</li><li>Mission and vision</li><li>Tracking</li><li>Contact us</li></ul>
  </div>
  <div class="footer-col abs" style="left:340px">
    <h5>Information</h5>
    <p>Fleet management specialists<br>Solutions</p>
    <p style="margin-top:14px">Follow us on</p>
    <div class="social"><span></span><span></span><span></span><span></span></div>
  </div>
  <div class="footer-col abs" style="left:600px">
    <h5>Newsletter</h5>
    <p>Lorem Ipsum is simply dummy<br>text of the printing.</p>
    <div class="news-field"><span>Email id</span><i><svg width="18" height="14" viewBox="0 0 18 14"><rect x="1" y="1" width="16" height="12" fill="#fff"/><path d="M1 1l8 7 8-7" fill="none" stroke="#3a8fd0" stroke-width="1.5"/></svg></i></div>
  </div>
  <div class="footer-col abs" style="left:881px">
    <h5>Keep In Touch</h5>
    <div class="touch-row"><svg width="22" height="18" viewBox="0 0 22 18"><path d="M11 1 1 9h3v8h5v-5h4v5h5V9h3z" fill="#9fb3e0"/></svg><span>418 W Harlow St Suite 210<br>Larkmoor, IL 60999</span></div>
    <div class="touch-row"><svg width="18" height="18" viewBox="0 0 24 24"><path d="M5 3h4l2 5-3 2a12 12 0 0 0 6 6l2-3 5 2v4a2 2 0 0 1-2 2A18 18 0 0 1 3 5a2 2 0 0 1 2-2z" fill="#9fb3e0"/></svg><span>555.014.2200<br>555.014.2202</span></div>
    <div class="touch-row"><svg width="18" height="14" viewBox="0 0 18 14"><rect x="1" y="1" width="16" height="12" fill="#9fb3e0"/><path d="M1 1l8 7 8-7" fill="none" stroke="#0f3aa3" stroke-width="1.5"/></svg><span>info@brightlanefreight.com</span></div>
  </div>
  <div class="copyright abs">Copyright © 2017 <b>Brightlane Freight</b>, All rights reserved.</div>
</footer>

</body>
</html>
```